Whitcombe Business Card Design

The name of the business is Dario Whitcombe, CPA LLC
The service that we offer is Accounting, Tax & Consulting Services. I need it to have the following items:
Dario Whitcombe, Principal
Phone Number
Email Address
Physical Address

I have attached the company logo, one in black and one in white. Please provide a design in black background and the other in white background. Please include "Accounting, Tax & Consulting Services". I want the business card to be clean and very professional.

```html
<!DOCTYPE html>
<html lang="en">
<head>
<meta charset="utf-8">
<title>Dario Whitcombe, CPA LLC — Business Card</title>
<link rel="stylesheet" href="https://fonts.googleapis.com/css2?family=Poppins:wght@400;500;600&display=swap">
<style>
  :root {
    --bg: #2a2a2a;
    --card-black: #0b0b0b;
    --brand-red: #9b161b;
    --white: #ffffff;
    --soft-white: #f2f2f2;
  }
  * { box-sizing: border-box; margin: 0; padding: 0; }
  html, body {
    width: 1200px; height: 1015px; overflow: hidden;
    background: var(--bg);
    font-family: "Poppins", sans-serif;
  }
  .canvas {
    width: 1200px; height: 1015px;
    display: flex; flex-direction: column; align-items: center; justify-content: center;
    gap: 30px;
  }
  .card {
    width: 820px; height: 468px;
    position: relative; overflow: hidden;
    box-shadow: 0 12px 30px rgba(0,0,0,.55);
  }

  /* Front */
  .card-front { background: var(--card-black); }
  .front-brand {
    position: absolute; left: 0; right: 0; top: 0; height: 330px;
    display: flex; align-items: center; justify-content: center; gap: 18px;
  }
  .brand-square { width: 26px; height: 26px; background: var(--brand-red); }
  .brand-name {
    color: var(--white); font-weight: 600; font-size: 38px; letter-spacing: 1px;
    text-transform: uppercase;
  }
  .service-band {
    position: absolute; left: 0; right: 0; bottom: 0; height: 138px;
    background: var(--brand-red);
    display: flex; align-items: center; justify-content: center;
    color: var(--white); font-weight: 500; font-size: 26px; letter-spacing: 1px;
    text-transform: uppercase;
  }

  /* Back */
  .card-back { background: var(--brand-red); }
  .contact {
    position: absolute; left: 70px; top: 70px; color: var(--white);
  }
  .contact-name { font-weight: 600; font-size: 34px; line-height: 1.1; }
  .contact-title { font-size: 22px; margin-bottom: 26px; }
  .contact-line { display: flex; align-items: center; gap: 14px; font-size: 22px; line-height: 1.6; }
  .contact-line svg { width: 24px; height: 24px; flex: none; }
  .contact-address { font-size: 22px; line-height: 1.35; margin-top: 20px; padding-left: 38px; }
  .back-brand {
    position: absolute; left: 0; right: 0; bottom: 0; height: 140px;
    background: var(--card-black);
    display: flex; align-items: center; justify-content: flex-end; gap: 18px;
    padding-right: 70px;
  }
  .back-brand .brand-name { font-size: 34px; }
</style>
</head>
<body>
<main class="canvas">
  <section class="card card-front" aria-label="Business card front">
    <div class="front-brand">
      <span class="brand-square"></span>
      <span class="brand-name">Dario Whitcombe, CPA LLC</span>
    </div>
    <div class="service-band">Accounting, Tax &amp; Consulting Services</div>
  </section>

  <section class="card card-back" aria-label="Business card back">
    <div class="contact">
      <p class="contact-name">Dario Whitcombe</p>
      <p class="contact-title">Principal</p>
      <p class="contact-line">
        <svg viewBox="0 0 24 24" fill="none" stroke="#fff" stroke-width="1.8"><rect x="2" y="2" width="20" height="20" rx="3"/><path d="M8 6.5l2 2.5-1.2 1.5c.9 1.8 2.2 3.1 4 4l1.5-1.2 2.5 2-1 1.8c-4.5-.2-8.4-4.1-8.6-8.6z" fill="#fff" stroke="none"/></svg>
        044-123 456 789
      </p>
      <p class="contact-line">
        <svg viewBox="0 0 24 24" fill="#fff"><path d="M2 5h20v14H2z"/><path d="M2 5l10 8 10-8" fill="none" stroke="#9b161b" stroke-width="1.6"/></svg>
        info@webname.com
      </p>
      <p class="contact-address">421, Address line here<br>Country Name, 45452</p>
    </div>
    <div class="back-brand">
      <span class="brand-square"></span>
      <span class="brand-name">Dario Whitcombe, CPA LLC</span>
    </div>
  </section>
</main>
</body>
</html>
```